Redesign of General Contractor Website

I currently have a wordpress site that needs some work. I would like to revitalize what we currently have to look more modern and up-to-date.
I want to be able to easily post pictures from new jobs and have a link to my own blog (not yet online). My current website can be found at www.brovikbuilders.com
the attached pictures are a site I built in Muse. i really like that sort of theme.
PLEASE NOTE: I am not interested in completely remaking the site, simply adding more functionalty and spicing it up a bit. (more animation, interactive elements, layering, etc...)
Target Market(s)
Property owners, Home owners, business owners, property managers, Decision makers purchasing a construction project, specifically Remodels, renovations, or damage restoration, with some or limited knowledge about how to complete one of those projects.
Industry/Entity Type
Contractor
Coding
Coded - Design and coding required
Number of Pages Required
1 page
Requirements
Must have
- Updateable photo bank displaying pictures from recent jobs that we can easily change and update. An embedded youtube pane showing our most recent video via our youtube channel. Animation and/or transition effects. The small circular logos must stay (I would like to see these be used with animation/transitional effects.
- Must be consistent with other marketing material. This can be found on our facebook page or in the power point file attached.
- Must use colors and fonts found at www.brovikbuilders.com
Nice to have
- Stock photos available if needed.
Should not have
- changes in logo design or re wording of text (use lorim ipsum if needed)
- No multiple pages, redesigning fonts

```html
<!DOCTYPE html>
<html lang="en">
<head>
<meta charset="utf-8">
<title>Brovik Builders</title>
<link href="https://fonts.googleapis.com/css2?family=Oswald:wght@500;600&family=Montserrat:wght@400;600;700&family=Open+Sans:ital,wght@0,400;0,600;0,700;1,400&display=swap" rel="stylesheet">
<style>
:root{
  --blue:#283a8f;
  --blue-deep:#1f2f78;
  --orange:#e2502a;
  --ink:#222;
  --muted:#555;
  --dark:#161616;
  --light:#f3f3f3;
  --white:#fff;
}
*{box-sizing:border-box;margin:0;padding:0}
html,body{width:1200px;height:4045px;overflow:hidden}
body{position:relative;font-family:"Open Sans",sans-serif;color:var(--ink);background:var(--white)}
.abs{position:absolute}
a{color:inherit;text-decoration:none}

/* header */
.site-header{left:0;top:0;width:1200px;height:116px;background:var(--white);z-index:3}
.brand{left:88px;top:0;width:160px;height:156px;border-radius:0 0 80px 80px;background:var(--white);display:flex;align-items:center;justify-content:center;text-align:center;font-family:"Montserrat",sans-serif;font-weight:700;font-size:25px;line-height:1.05;color:var(--blue);z-index:4}
.top-contact{right:100px;top:20px;display:flex;gap:26px;font-size:15px;color:var(--ink);align-items:center}
.top-contact span{display:flex;align-items:center;gap:8px}
.dot-icon{width:26px;height:26px;border-radius:50%;background:var(--orange);display:inline-flex;align-items:center;justify-content:center}
.main-nav{right:100px;top:76px;display:flex;gap:28px;font-family:"Montserrat",sans-serif;font-size:13px;font-weight:600;color:var(--ink)}
.main-nav .active{color:var(--blue);border-bottom:2px solid var(--blue);padding-bottom:4px}

/* hero */
.hero{left:0;top:116px;width:1200px;height:558px;background:linear-gradient(100deg,#3d3b2f 0%,#6a6a55 38%,#7c7b70 60%,#4b4c4e 100%)}
.hero-title{left:100px;top:300px;font-family:"Oswald",sans-serif;font-weight:600;font-size:42px;line-height:1.12;color:var(--white);text-transform:uppercase}
.hero-sub{left:100px;top:395px;font-size:17px;font-weight:600;color:var(--white);line-height:1.45}
.btn-orange{left:100px;top:460px;width:134px;height:36px;border-radius:18px;background:var(--orange);color:var(--white);font-size:13px;font-weight:700;display:flex;align-items:center;justify-content:center;text-transform:uppercase}
.dots{display:flex;gap:9px}
.dots i{width:12px;height:12px;border-radius:50%;background:var(--white);display:block}
.dots i.on{box-shadow:0 0 0 3px rgba(255,255,255,.5)}

/* welcome */
.video{left:102px;top:760px;width:478px;height:278px;background:linear-gradient(135deg,#2c2c2c,#6d6d6d 55%,#3a3a3a)}
.video-play{left:240px;top:120px;width:0;height:0;border-left:0}
.welcome-title{left:626px;top:694px;font-family:"Montserrat",sans-serif;font-size:27px;color:var(--ink)}
.welcome-title b{color:var(--blue);font-weight:600}
.welcome-text{left:626px;top:810px;width:470px;font-size:12px;line-height:1.7;color:var(--muted)}
.welcome-text p+p{margin-top:14px}
.btn-blue{left:626px;top:992px;width:106px;height:34px;background:var(--blue);color:var(--white);font-size:12px;font-weight:600;display:flex;align-items:center;justify-content:center}

/* services */
.services{left:0;top:1133px;width:1200px;height:660px;background:linear-gradient(180deg,var(--blue) 0%,var(--blue-deep) 100%)}
.section-title-light{width:1200px;text-align:center;font-family:"Montserrat",sans-serif;font-size:36px;font-weight:600;color:var(--white)}
.services-intro{left:180px;top:1245px;width:840px;text-align:center;font-size:12px;line-height:1.75;color:var(--white)}
.service{width:320px;height:130px;color:var(--white)}
.service-icon{left:0;top:0;width:72px;height:72px;border-radius:50%;background:var(--orange);display:flex;align-items:center;justify-content:center}
.service h3{left:90px;top:8px;font-family:"Montserrat",sans-serif;font-weight:600;font-size:19px;text-transform:uppercase}
.service p{left:90px;top:42px;width:220px;font-size:12px;line-height:1.6}
.service .more{left:90px;top:110px;font-size:11px;font-weight:600;text-transform:uppercase}

/* roof band */
.roof-band{left:0;top:1793px;width:1200px;height:292px;background:linear-gradient(100deg,#3a3a32 0%,#2a2a2a 40%,#333 100%)}
.roof-band-text{left:0;top:1908px;width:1200px;text-align:center;font-family:"Montserrat",sans-serif;font-weight:700;font-size:26px;line-height:1.35;color:var(--white);text-transform:uppercase}

/* work */
.section-title-dark{width:1200px;text-align:center;font-family:"Montserrat",sans-serif;font-size:33px;color:var(--ink)}
.work-grid{left:100px;top:2228px;width:998px;height:410px}
.tile{position:absolute}
.tile.featured{left:0;top:0;width:332px;height:410px;border:9px solid var(--orange);background:linear-gradient(180deg,#a9c1d6 0%,#9a8d6e 45%,#6e7a4e 60%,#a9c1d6 62%,#8b8a7f 100%)}
.t1{left:336px;top:0;width:328px;height:200px;background:linear-gradient(180deg,#c9d6df 0%,#7b6a55 55%,#8e9a5f 100%)}
.t2{left:668px;top:0;width:330px;height:200px;background:linear-gradient(180deg,#c6d8e6 0%,#8a5e46 55%,#8f9566 100%)}
.t3{left:336px;top:206px;width:364px;height:204px;background:linear-gradient(180deg,#b3aa98 0%,#8b7b68 55%,#a59d7c 100%)}
.t4{left:704px;top:206px;width:294px;height:204px;background:linear-gradient(180deg,#c9dbe8 0%,#846b59 55%,#9e9e7a 100%)}

/* interior band */
.interior-band{left:0;top:2732px;width:1200px;height:383px;background:linear-gradient(180deg,#4a4540 0%,#2f2c29 60%,#3b3631 100%)}
.interior-text{left:150px;top:2858px;width:900px;text-align:center;font-family:"Montserrat",sans-serif;font-weight:700;font-size:25px;line-height:1.45;color:var(--white);text-transform:uppercase}

/* team */
.team{left:0;top:3115px;width:1200px;height:396px;background:var(--light)}
.team-title{left:0;top:3180px;width:1200px;text-align:center;font-family:"Montserrat",sans-serif;font-size:28px;color:var(--ink)}
.team-title::after{content:"";display:block;width:60px;height:2px;background:var(--blue);margin:12px auto 0}
.member{width:480px;height:130px}
.avatar{left:0;top:0;width:120px;height:120px;border-radius:50%;border:4px solid #ddd;background:linear-gradient(180deg,#b0a49a,#8a7e74)}
.member blockquote{left:140px;top:0;width:340px;font-size:12px;font-style:italic;line-height:1.6;color:var(--muted)}
.member .name{left:140px;top:78px;font-size:13px;font-weight:600;color:var(--blue);line-height:1.6;text-transform:none}

/* contact */
.contact{left:0;top:3511px;width:1200px;height:475px;background:var(--dark)}
.contact-title{left:0;top:3556px;width:1200px;text-align:center;font-family:"Montserrat",sans-serif;font-size:31px;color:var(--white)}
.contact-intro{left:300px;top:3612px;width:600px;text-align:center;font-size:12px;line-height:1.8;color:var(--white)}
.field{width:278px;height:36px;border:1px solid #888;font-size:11px;color:var(--white);padding:10px 10px}
.message{left:461px;top:3738px;width:273px;height:140px;border:1px solid #888;font-size:11px;color:var(--white);padding:10px}
.submit{left:316px;top:3900px;width:272px;height:34px;background:var(--blue);color:var(--white);font-size:13px;font-weight:700;display:flex;align-items:center;justify-content:center}
.info-title{left:785px;top:3732px;font-family:"Montserrat",sans-serif;font-size:20px;font-weight:600;color:var(--white)}
.info-list{left:785px;top:3785px;display:flex;flex-direction:column;gap:20px;font-size:12px;color:#bbb}
.info-list li{list-style:none;display:flex;align-items:center;gap:14px}

/* footer */
.site-footer{left:0;top:3986px;width:1200px;height:59px;background:#0c0c0c;border-top:1px solid #333;color:var(--white);font-size:11px}
.site-footer .copy{left:100px;top:22px}
.site-footer .social{right:100px;top:14px;display:flex;gap:10px;align-items:center}
.social i{width:28px;height:28px;border-radius:50%;background:var(--white);display:block}
</style>
</head>
<body>

<header class="site-header abs">
  <div class="brand abs">Brovik<br>Builders</div>
  <div class="top-contact abs">
    <span><i class="dot-icon"><svg width="12" height="12" viewBox="0 0 24 24"><path fill="#fff" d="M6.6 10.8a15 15 0 006.6 6.6l2.2-2.2c.3-.3.7-.4 1-.2 1.1.4 2.3.6 3.6.6.6 0 1 .4 1 1V20c0 .6-.4 1-1 1A17 17 0 013 4c0-.6.4-1 1-1h3.5c.6 0 1 .4 1 1 0 1.3.2 2.5.6 3.6.1.3 0 .7-.2 1z"/></svg></i>(855) 410-2287</span>
    <span><i class="dot-icon"><svg width="12" height="12" viewBox="0 0 24 24"><path fill="#fff" d="M2 5h20v14H2zm2 2v.5l8 5 8-5V7z"/></svg></i>info@brovikbuilders.com</span>
  </div>
  <nav class="main-nav abs">
    <a class="active">HOME</a><a>ABOUT US</a><a>OUR WORK</a><a>OUR SERVICES</a><a>BLOG</a><a>CONTACT US</a>
  </nav>
</header>

<section class="hero abs" role="img" aria-label="Photo of a roofer installing shingles on a house roof"></section>
<h1 class="hero-title abs">Has your home been<br>through hail and back?</h1>
<p class="hero-sub abs">Call Us Today for Your no Obligation Quote.<br>(855) 410-2287</p>
<a class="btn-orange abs">Find out more</a>
<div class="dots abs" style="left:102px;top:522px"><i class="on"></i><i></i><i></i><i></i></div>

<div class="video abs" role="img" aria-label="Embedded video preview from the company channel"></div>
<h2 class="welcome-title abs">WELCOME TO <b>BROVIK BUILDERS</b></h2>
<div class="welcome-text abs">
  <p>Brovik Builders takes a customer oriented approach to solving all of our client's needs. Realizing that no two projects are ever the same, Brovik Builders uses forward thinking techniques to satisfy our customers. While most contracting companies use construction methods that are over half of a century old, Brovik Builders sets the bar in innovative thinking. With our team of certified adjusters.</p>
  <p>we work hand in hand with our customers to provide unprecedented customer service and the utmost efficiency.</p>
</div>
<a class="btn-blue abs">READ MORE</a>

<section class="services abs" role="img" aria-label="Blue tinted photo of a worker on a roof"></section>
<h2 class="section-title-light abs" style="left:0;top:1185px">OUR SERVICES</h2>
<p class="services-intro abs">Brovik Builders provides professional services for our customer homes. We work with you to assess your specific needs and guarantee you a custom solution. Although we specialize in insurance claims, our experts offer a wide range of services with customized service to ensure you get exactly what you need when you need it. In addition to roof repair and installation we offer a preventive maintenance program entitled the Roof Quality Preservation</p>

<div class="service abs" style="left:100px;top:1376px">
  <div class="service-icon abs"><svg width="36" height="36" viewBox="0 0 36 36" fill="none" stroke="#fff" stroke-width="3"><path d="M4 20L18 8l14 12"/><path d="M9 16v14h18V16"/></svg></div>
  <h3 class="abs">Roofing</h3>
  <p class="abs">One of the most important parts of your home is the roof. Your roof protects your home from the elements</p>
  <a class="more abs">Read more ›</a>
</div>
<div class="service abs" style="left:456px;top:1376px">
  <div class="service-icon abs"><svg width="36" height="36" viewBox="0 0 36 36" fill="none" stroke="#fff" stroke-width="3"><path d="M6 10h24M6 18h24M6 26h24"/></svg></div>
  <h3 class="abs">Siding</h3>
  <p class="abs">Old, deteriorating, or damaged siding can leave your house looking incomplete and can pose</p>
  <a class="more abs">Read more ›</a>
</div>
<div class="service abs" style="left:801px;top:1376px">
  <div class="service-icon abs"><svg width="36" height="36" viewBox="0 0 36 36" fill="none" stroke="#fff" stroke-width="3"><path d="M8 8v20h20M16 8v12h12"/></svg></div>
  <h3 class="abs">Gutters</h3>
  <p class="abs">By diverting water from the base of the building, rain gutters help guard against erosion, leaks, foundation damage</p>
  <a class="more abs">Read more ›</a>
</div>
<div class="service abs" style="left:100px;top:1556px">
  <div class="service-icon abs"><svg width="36" height="36" viewBox="0 0 36 36" fill="none" stroke="#fff" stroke-width="3"><rect x="7" y="7" width="22" height="22"/><path d="M18 7v22M7 18h22"/></svg></div>
  <h3 class="abs">Windows</h3>
  <p class="abs">Rooftops and siding aren't the only parts of your home or business vulnerable to the elems</p>
  <a class="more abs">Read more ›</a>
</div>
<div class="service abs" style="left:456px;top:1556px">
  <div class="service-icon abs"><svg width="36" height="36" viewBox="0 0 36 36" fill="none" stroke="#fff" stroke-width="3"><path d="M6 24l16-16 8 8-16 16z"/></svg></div>
  <h3 class="abs">Drywall</h3>
  <p class="abs">If you're having issues with drywall, or if you'd simply like to have drywall professionally installed, we're</p>
  <a class="more abs">Read more ›</a>
</div>
<div class="service abs" style="left:801px;top:1556px">
  <div class="service-icon abs"><svg width="36" height="36" viewBox="0 0 36 36" fill="none" stroke="#fff" stroke-width="3"><path d="M9 30V10M15 30V8M21 30V8M27 30V10M5 16h26M5 24h26"/></svg></div>
  <h3 class="abs">Fences</h3>
  <p class="abs">Our work on fences is second to none as we are experienced in the most popular styles of fencing</p>
  <a class="more abs">Read more ›</a>
</div>
<div class="dots abs" style="left:568px;top:1731px"><i class="on"></i><i></i><i></i><i></i></div>

<section class="roof-band abs" role="img" aria-label="Photo of a worker in a hard hat on a dark metal roof"></section>
<p class="roof-band-text abs">Did you know that roof durability<br>options range from 20-50 years?</p>

<h2 class="section-title-dark abs" style="left:0;top:2138px">OUR WORK</h2>
<div class="work-grid abs">
  <div class="tile featured" role="img" aria-label="Photos of two finished brick houses"></div>
  <div class="tile t1" role="img" aria-label="Photo of a finished brick ranch house"></div>
  <div class="tile t2" role="img" aria-label="Photo of a brick home with new roof"></div>
  <div class="tile t3" role="img" aria-label="Photo of a homeowner in front of a renovated house"></div>
  <div class="tile t4" role="img" aria-label="Photo of a brick house with new roof"></div>
</div>

<section class="interior-band abs" role="img" aria-label="Photo of an interior room being painted with paint cans on the floor"></section>
<p class="interior-text abs">Although we specialize in roof repair and installations, we are also known for our sheetrock and painting expertise.</p>

<section class="team abs"></section>
<h2 class="team-title abs">THE TEAM</h2>
<div class="member abs" style="left:97px;top:3292px">
  <div class="avatar abs" role="img" aria-label="Portrait of Dale Brovik"></div>
  <blockquote class="abs">" Nemo enim ipsam voluptatem quia voluptas sit aspernatur aut odit aut fugit, sed quia consequuntur magni dolores eos qui ratione voluptatem sequi nesciunt.</blockquote>
  <p class="name abs">DALE BROVIK -<br>Owner Brovik Builders</p>
</div>
<div class="member abs" style="left:634px;top:3292px">
  <div class="avatar abs" role="img" aria-label="Portrait of Ross Brovik"></div>
  <blockquote class="abs">" Nemo enim ipsam voluptatem quia voluptas sit aspernatur aut odit aut fugit, sed quia consequuntur magni dolores eos qui ratione voluptatem sequi nesciunt.</blockquote>
  <p class="name abs">ROSS BROVIK -<br>Manager Brovik Builders</p>
</div>

<section class="contact abs"></section>
<h2 class="contact-title abs">CONTACT US</h2>
<p class="contact-intro abs">Thank you for visiting our website. For questions, comments, or suggestions please fill out the form below. To schedule a free inspection call us directly at (855) 410-2287.<br><br>-Best Regards<br>The Brovik Builders Team</p>
<div class="field abs" style="left:167px;top:3738px">Name :</div>
<div class="field abs" style="left:167px;top:3790px">Email :</div>
<div class="field abs" style="left:167px;top:3842px">Phone :</div>
<div class="message abs">Message :</div>
<a class="submit abs">SUBMIT</a>
<h3 class="info-title abs">CONTACT INFO</h3>
<ul class="info-list abs">
  <li><svg width="16" height="20" viewBox="0 0 16 20"><path fill="#bbb" d="M8 0a8 8 0 00-8 8c0 6 8 12 8 12s8-6 8-12a8 8 0 00-8-8zm0 11a3 3 0 110-6 3 3 0 010 6z"/></svg>418 Alder Ave, Millbrook, TX 76500</li>
  <li><svg width="16" height="16" viewBox="0 0 24 24"><path fill="#bbb" d="M6.6 10.8a15 15 0 006.6 6.6l2.2-2.2c.3-.3.7-.4 1-.2 1.1.4 2.3.6 3.6.6.6 0 1 .4 1 1V20c0 .6-.4 1-1 1A17 17 0 013 4c0-.6.4-1 1-1h3.5c.6 0 1 .4 1 1 0 1.3.2 2.5.6 3.6.1.3 0 .7-.2 1z"/></svg>(855) 410-2287</li>
  <li><svg width="16" height="14" viewBox="0 0 24 20"><path fill="none" stroke="#bbb" stroke-width="2" d="M2 2h20v16H2zM2 3l10 8 10-8"/></svg>info@brovikbuilders.com</li>
</ul>

<footer class="site-footer abs">
  <p class="copy abs">© Brovik Builders ©2017. All Rights Reserved.</p>
  <div class="social abs"><span>Connect with our social network :</span><i></i><i></i><i></i></div>
</footer>

</body>
</html>
```